Local Roofing/Construction company business needs new biz card design

We need a new business card design, current cards are from the start of this operation and generic at best. We are a local Construction Company (General Contractor) with a majority of our work originating from insurance claims-exterior finish work is the main focus (Roofs-Siding-Gutters etc). Heavily involved with homeowners and the low ball offers they receive from insurance company's after a insurable event takes place. I have attached some of our original logo file(s) below.

```html
<!DOCTYPE html>
<html lang="en">
<head>
<meta charset="utf-8">
<title>Stoneline Builders – Business Card</title>
<link href="https://fonts.googleapis.com/css2?family=Figtree:wght@400;500;700;800&display=swap" rel="stylesheet">
<style>
  :root{
    --green:#4fb56b;
    --ink:#0f2226;
    --text:#5f6366;
    --card:#ffffff;
    --backdrop:#e6e6e6;
  }
  *{margin:0;padding:0;box-sizing:border-box}
  html,body{width:1200px;height:1200px;overflow:hidden;background:var(--backdrop);font-family:"Figtree",sans-serif}
  .card{position:absolute;left:235px;width:730px;height:417px;background:var(--card);box-shadow:0 6px 18px rgba(0,0,0,.18)}
  .card--front{top:160px}
  .card--back{top:630px}
  .abs{position:absolute;white-space:nowrap}

  /* front */
  .brand{left:0;right:0;top:96px;display:flex;justify-content:center;align-items:center;gap:14px}
  .brand__mark{width:44px;height:44px;background:var(--green);border-radius:6px}
  .brand__name{font-size:34px;font-weight:800;color:var(--ink);letter-spacing:.5px}
  .specialties__title{left:138px;top:236px;font-size:26px;font-weight:800;color:var(--green);letter-spacing:.2px}
  .specialty{display:flex;align-items:center;gap:9px;font-size:20px;color:var(--text)}
  .specialty svg{width:25px;height:25px;flex:none}

  /* back */
  .back-mark{left:579px;top:51px;width:107px;height:92px;background:var(--green);border-radius:12px}
  .back-mark__name{left:560px;top:150px;width:145px;text-align:center;font-size:13px;font-weight:800;color:var(--green)}
  .person__name{left:47px;top:218px;font-size:31px;font-weight:800;color:var(--green)}
  .person__role{left:47px;top:253px;font-size:19px;color:var(--text)}
  .contact{left:45px;display:flex;align-items:center;gap:9px;font-size:19px;color:var(--text)}
  .contact svg{width:17px;height:17px;flex:none}
  .address{right:46px;top:313px;text-align:right;font-size:19px;line-height:26px;color:var(--text)}
</style>
</head>
<body>

<section class="card card--front">
  <div class="abs brand">
    <span class="brand__mark"></span>
    <span class="brand__name">STONELINE BUILDERS</span>
  </div>

  <h2 class="abs specialties__title">OUR CONTRACTING SPECIALTIES</h2>

  <div class="abs specialty" style="left:137px;top:297px">
    <svg viewBox="0 0 24 24"><circle cx="12" cy="12" r="12" fill="var(--green)"/><path d="M6 12l6-5 6 5M8 11v6h8v-6" fill="none" stroke="#fff" stroke-width="1.3"/></svg>
    Residential Roofing
  </div>
  <div class="abs specialty" style="left:137px;top:336px">
    <svg viewBox="0 0 24 24"><circle cx="12" cy="12" r="12" fill="var(--green)"/><path d="M7 18V9l5-3 5 3v9zM10 18v-4h4v4" fill="none" stroke="#fff" stroke-width="1.3"/></svg>
    Commercial Roofing
  </div>
  <div class="abs specialty" style="left:394px;top:298px">
    <svg viewBox="0 0 24 24"><circle cx="12" cy="12" r="12" fill="var(--green)"/><path d="M7 7h10v10H7zM7 10.3h10M7 13.6h10M10.3 7v10M13.6 7v10" fill="none" stroke="#fff" stroke-width="1.1"/></svg>
    Exterior Finishes
  </div>
  <div class="abs specialty" style="left:394px;top:337px">
    <svg viewBox="0 0 24 24"><circle cx="12" cy="12" r="12" fill="var(--green)"/><path d="M7 17l5-4 5 4M9 7v2M12 6v2M15 7v2" fill="none" stroke="#fff" stroke-width="1.3"/></svg>
    Storm Restoration
  </div>
</section>

<section class="card card--back">
  <div class="abs back-mark"></div>
  <div class="abs back-mark__name">STONELINE BUILDERS</div>

  <div class="abs person__name">Marcus Dale</div>
  <div class="abs person__role">Founder &amp; Director</div>

  <div class="abs contact" style="top:286px">
    <svg viewBox="0 0 24 24"><path d="M6 3l4 4-2 3c1 3 3 5 6 6l3-2 4 4-3 3C10 20 4 14 3 6z" fill="var(--green)"/></svg>
    555-014-2290
  </div>
  <div class="abs contact" style="top:314px">
    <svg viewBox="0 0 24 24"><rect x="2" y="5" width="20" height="14" fill="var(--green)"/><path d="M2 6l10 7 10-7" fill="none" stroke="#fff" stroke-width="1.6"/></svg>
    hello@stonelinebuilders.com
  </div>
  <div class="abs contact" style="top:342px">
    <svg viewBox="0 0 24 24"><circle cx="12" cy="12" r="10" fill="var(--green)"/><path d="M2 12h20M12 2c-4 5-4 15 0 20M12 2c4 5 4 15 0 20" fill="none" stroke="#fff" stroke-width="1.3"/></svg>
    stonelinebuilders.com
  </div>

  <address class="abs address" style="font-style:normal">245 Birch Hollow Rd<br>Maple Falls, MO 63000</address>
</section>

</body>
</html>
```